Design and Renovation Company Luxury Business Card

I want to create a luxury business card for a Design and Renovation Firm . We will use our current logo. The company name is 528BUILDA. We do not want anything standard. We need a very unique concept.
Please see uploaded inspiration. I really like the textured paper option. I would like the card to be thick with debossing, and/or embossing options. The logo has orange in it but I would like to see the card with and without the orange. I think the orange may make the company feel less high-end. The goal is to elevate the logo not match its vibe per se of the logo. We want something very unique, not standard at all!
I would like a space for :
Logo,
Name,
Position,
Email,
Office number,
Website Address,
Business Address,
Thank you!
Have fun!
Target Market(s)
Home owners Age 35 +
Industry/Entity Type
Design and Renovation
Contact Information for Business Card
Logo, Name, Position, Email, Office number, Website Address, Business Address,.
Colors
Designer to choose colors to be used in the design.
Requirements
Must have
- A luxury designer feel. Must be black or dark grey but open to other luxury ideas.
Nice to have
- Gold, silver, black embossing or debossing. Textured paper design.
Should not have
- A cheap look and feel.

```html
<!DOCTYPE html>
<html lang="en">
<head>
<meta charset="utf-8">
<title>528BUILDA Business Card</title>
<link rel="stylesheet" href="https://fonts.googleapis.com/css2?family=Arimo:wght@400;700&display=swap">
<style>
  :root {
    --backdrop: #c9c9c9;
    --orange: #e38a1e;
    --white: #f7f7f7;
    --charcoal: #2a2a2a;
    --deboss: #1c1c1c;
    --card-edge: #e9e9e9;
  }
  html, body {
    margin: 0;
    padding: 0;
    width: 1200px;
    height: 800px;
    overflow: hidden;
    background: var(--backdrop);
    font-family: "Arimo", Arial, sans-serif;
  }
  .canvas {
    position: relative;
    width: 1200px;
    height: 800px;
  }
  .card {
    position: absolute;
    top: 250px;
    width: 525px;
    height: 300px;
    border-radius: 24px;
    box-shadow: 0 0 0 2px var(--card-edge);
    overflow: hidden;
  }
  .card--front {
    left: 50px;
    background: var(--orange);
    color: var(--white);
  }
  .card--back {
    left: 625px;
    background: var(--charcoal);
  }

  /* Front face */
  .brand-name {
    position: absolute;
    left: 44px;
    top: 134px;
    margin: 0;
    font-weight: 700;
    font-size: 22px;
    color: var(--white);
  }
  .contact {
    position: absolute;
    left: 258px;
    top: 60px;
    line-height: 1.25;
  }
  .contact__name {
    margin: 0;
    font-weight: 700;
    font-size: 22px;
  }
  .contact__role {
    margin: 0 0 14px;
    font-size: 15px;
  }
  .contact__address {
    margin: 0 0 14px;
    font-style: normal;
    font-size: 15px;
  }
  .contact__lines {
    margin: 0;
    padding: 0;
    list-style: none;
    font-size: 15px;
  }
  .contact__label {
    font-weight: 700;
  }

  /* Back face */
  .back-brand {
    position: absolute;
    left: 0;
    right: 0;
    top: 100px;
    text-align: center;
    color: var(--deboss);
  }
  .back-brand__name {
    margin: 0;
    font-weight: 400;
    font-size: 62px;
    line-height: 1;
  }
  .back-brand__tagline {
    margin: 18px 0 0;
    font-size: 15px;
    font-weight: 400;
  }
</style>
</head>
<body>
<main class="canvas">
  <section class="card card--front" aria-label="Business card front">
    <p class="brand-name">528BUILDA</p>
    <div class="contact">
      <p class="contact__name">Marcus Hale</p>
      <p class="contact__role">President</p>
      <address class="contact__address">4127 Ashford Lane<br>Glen Ridge, NY 11042</address>
      <ul class="contact__lines">
        <li><span class="contact__label">P :</span> (555) 0142-7788</li>
        <li><span class="contact__label">E :</span> name@528BUILDA.com</li>
        <li><span class="contact__label">W :</span> www.528BUILDA.com</li>
      </ul>
    </div>
  </section>

  <section class="card card--back" aria-label="Business card back">
    <div class="back-brand">
      <p class="back-brand__name">528BUILDA</p>
      <p class="back-brand__tagline">Design and Renovation Firm</p>
    </div>
  </section>
</main>
</body>
</html>
```